Tech Website

1. Overview
Prism48, formally named LumoVista, is a pioneer in computer vision technology and machine learning. Based out of Santa Clara, California, Prism48 is at the forefront of the User Interface revolution; building technology architecture that grants devices with the aptitude to respond to emotional detection, gaze tracking, facial recognition, age and gender identification and gaming interaction. Winner of the Mobile Track at NOVA Founders Sprint 2012, Prism48 has developed the next generation of consumer behaviour analytics. Prism48 software solutions are scalable across various platforms including mobile phone, tablets, PC and SmartTV.
Updates

Good day, 

Please see the update to our brief - there is a PDF of the type of format and design we are looking for.  It shows each page - Landing, Technology, Product, Press and Company.

Thank you for your designs

Regards,

Target Market(s)

Target market - A mix of enterprise and consumer audiences, targeting the need for the technology in the living room space

Industry/Entity Type

Architecture

Requirements
Must have
• Design preferences - Easy to navigate, modern with sleek feel, trendy, tech saavy, using cube as a consistent element/theme. colours are not determined, but parrot green was one idea with 2 additional underlying colours. keys words like user interface revolution or sense recognition are good sources to draw inspiration.

Landing page will have a video - illustrating different uses of technology

Technical Specs - Landing page, 6 tabs/subpages, and each subpage may have 1 or 2 additional pages. Coding will be necessary, not that much at the beginning stages.

```html
<!DOCTYPE html>
<html lang="en">
<head>
<meta charset="utf-8">
<title>Prism48 — Computer Vision Technology</title>
<link rel="stylesheet" href="https://fonts.googleapis.com/css2?family=Arimo:wght@400&family=Open+Sans:wght@300;400&display=swap">
<style>
  :root {
    --green: #6cb33e;
    --green-text: #5b9a1f;
    --lime: #a8d43f;
    --dark: #2c2c2c;
    --hero: #2e2e2e;
    --body-text: #555;
    --muted: #888;
    --teal: #2b9bb5;
    --sky: #3aa6d6;
    --link-red: #b03030;
    --panel: #e6e6e6;
    --white: #fff;
  }
  * { box-sizing: border-box; margin: 0; padding: 0; }
  html, body { width: 1150px; height: 1200px; overflow: hidden; background: var(--white); }
  body { position: relative; font-family: "Arimo", Arial, sans-serif; color: var(--body-text); }
  .abs { position: absolute; }

  /* header */
  .site-header { left: 0; top: 0; width: 1150px; height: 83px;
    background: linear-gradient(#fff, #f4f4f4); border-bottom: 3px solid var(--green); }
  .brand { left: 86px; top: 14px; font-family: "Open Sans", sans-serif; font-weight: 300;
    font-size: 42px; color: var(--green); line-height: 50px; display: flex; align-items: center; gap: 10px; }
  .brand-mark { width: 14px; height: 14px; background: var(--green); }
  .main-nav a { position: absolute; top: 30px; font-size: 14px; color: #555; text-decoration: none; transform: translateX(-50%); white-space: nowrap; }
  .main-nav .active-tab { left: 507px; top: 10px; width: 78px; height: 70px; background: linear-gradient(#82c342, #5fa52c);
    border-radius: 3px 3px 0 0; position: absolute; }
  .main-nav a.active { color: #fff; }

  /* hero */
  .hero { left: 0; top: 83px; width: 1150px; height: 380px; background: var(--hero); }
  .hero-fade { left: 0; top: 463px; width: 1150px; height: 60px; background: linear-gradient(#ececec, #fff); }
  .hero-device { left: 90px; top: 100px; width: 435px; height: 410px; border-radius: 26px;
    background: linear-gradient(110deg, #4a4a4a, #222 45%, #6a4f6d 60%, #2a2a2a); }
  .hero-title { left: 523px; top: 162px; width: 560px; font-family: "Open Sans", sans-serif; font-weight: 300;
    font-size: 32px; line-height: 48px; color: var(--lime); letter-spacing: -0.3px; }
  .hero-copy { left: 523px; top: 270px; width: 525px; font-size: 12px; line-height: 22px; color: #ddd; text-align: justify; }
  .slider-dots { left: 939px; top: 422px; display: flex; gap: 21px; }
  .slider-dots span { width: 10px; height: 10px; border-radius: 50%; background: #fff; }
  .slider-dots span.on { background: var(--green); }

  /* intro */
  .section-title { font-size: 21px; color: var(--green-text); font-weight: 400; }
  .welcome-title { left: 92px; top: 532px; }
  .welcome-copy { left: 92px; top: 572px; width: 656px; font-size: 12px; line-height: 22px; text-align: justify; }
  .video-title { left: 770px; top: 499px; width: 288px; text-align: center; }
  .video-player { left: 770px; top: 535px; width: 288px; height: 163px; background: #000; padding: 3px; }
  .video-frame { width: 100%; height: 141px; background: radial-gradient(circle at 55% 45%, #4c5a63, #1b1f22 75%); position: relative; }
  .play-btn { position: absolute; left: 127px; top: 61px; width: 32px; height: 22px; background: #111; border-radius: 4px; }
  .play-btn::after { content: ""; position: absolute; left: 12px; top: 5px; border-left: 10px solid #fff; border-top: 6px solid transparent; border-bottom: 6px solid transparent; }
  .video-bar { height: 3px; background: #444; margin-top: 2px; position: relative; }
  .video-bar i { position: absolute; left: 0; top: 0; width: 66px; height: 3px; background: #c00; }
  .video-controls { height: 12px; }

  .divider { left: 190px; top: 739px; width: 770px; height: 1px; background: linear-gradient(90deg, transparent, #e2e2e2, transparent); }

  /* columns */
  .col-title { top: 777px; }
  .about-title { left: 92px; }
  .news-icon { left: 422px; top: 778px; width: 22px; height: 18px; border: 1px solid #bbb; background: #f2f2f2; }
  .news-title { left: 457px; }
  .tweet-icon { left: 761px; top: 773px; width: 28px; height: 28px; border-radius: 50%; background: var(--sky); }
  .tweets-title { left: 798px; color: var(--sky); }
  .about-image { left: 92px; top: 820px; width: 304px; height: 121px; border: 1px solid #ddd;
    background: linear-gradient(90deg, #e9ecef, #9fb7c9 40%, #2d3338 55%, #c5d2dc 75%, #eef0f2); }
  .about-copy { left: 92px; top: 955px; width: 304px; font-size: 12px; line-height: 22px; }

  .news-item { left: 422px; width: 306px; }
  .news-thumb { position: absolute; left: 0; top: 0; width: 84px; height: 60px; border: 1px solid #ccc; }
  .news-text { position: absolute; left: 99px; top: 0; width: 210px; font-size: 12px; line-height: 20px; }
  .news-date { position: absolute; left: 99px; top: 46px; font-size: 12px; color: var(--green-text); }

  .view-all { top: 1056px; height: 27px; background: var(--panel); font-size: 12px; text-align: right; padding: 7px 12px; }
  .view-all a { color: #555; }

  .tweet { left: 760px; width: 290px; }
  .tweet-avatar { position: absolute; left: 0; top: 0; width: 32px; height: 32px; border: 1px solid #ddd; }
  .tweet-text { position: absolute; left: 42px; top: -3px; width: 245px; font-size: 11px; line-height: 17px; text-align: justify; color: #444; }
  .tweet-text .user { color: var(--teal); }
  .tweet-text a { color: var(--link-red); }
  .tweet-meta { position: absolute; left: 42px; top: 73px; font-size: 9px; color: var(--teal); white-space: nowrap; }

  /* footer */
  .site-footer { left: 0; top: 1119px; width: 1150px; height: 81px; background: var(--dark); }
  .footer-nav { left: 86px; top: 1139px; font-size: 12px; color: #ddd; word-spacing: 2px; }
  .copyright { left: 86px; top: 1169px; font-size: 12px; color: #ddd; }
  .social { top: 1148px; width: 26px; height: 26px; border-radius: 50%; background: #fff; }
</style>
</head>
<body>

<header class="abs site-header">
  <div class="abs brand"><span class="brand-mark"></span>Prism48</div>
  <nav class="main-nav">
    <span class="active-tab"></span>
    <a class="active" style="left:547px">Home</a>
    <a style="left:660px">About us</a>
    <a style="left:780px">Services</a>
    <a style="left:897px">Product</a>
    <a style="left:1012px">Contact</a>
  </nav>
</header>

<section class="abs hero"></section>
<div class="abs hero-fade"></div>
<div class="abs hero-device" role="img" aria-label="Smartphone shown from the back, front and side"></div>
<h1 class="abs hero-title" style="font-weight:300">Allows mobile applications to leverage Front Facing Camera.</h1>
<p class="abs hero-copy">Cras porta ultricies quam, id ullamcorper augue interdum vitae. Lorem ipsum dolor sit amet, con sectetur adipiscing elit. Aenean commodo vulputate ligula vel porttitor. Nullam eu quam nunc. Praesent dapibus egestas odio eu sagittis. Quisque sagittis urna eu dolor pretium feugiat.</p>
<div class="abs slider-dots"><span class="on"></span><span></span><span></span><span></span></div>

<h2 class="abs section-title welcome-title">Welcome to our site</h2>
<p class="abs welcome-copy">Praesent nibh augue, luctus id dapibus ut, malesuada egestas sem. In mollis orci in velit posuere varius. Curabitur cursus arcu eget lacus blandit et consequat nibh mattis. Aliquam aliquam ultricies risus, pulvinar porta neque posuere ac. Nam pretium luctus libero, eget laoreet turpis facilisis quis. Etiam lobortis odio vitae risus pharetra congue. In nulla mi, aliquam sit amet hendrerit eu, ultrices ut urna. Curabitur quis dui mauris. Praesent magna risus, lobortis id vehicula facilisis, lacinia ac lorem. Vestibulum imperdiet imperdiet nibh, in blandit enim feugiat eu. Morbi quam magna, pulvinar quis feugiat eu, feugiat ut orci. Curabitur quis dolor ut orci dapibus scelerisque ultricies in tortor.</p>

<h2 class="abs section-title video-title">Uses of Technology</h2>
<div class="abs video-player">
  <div class="video-frame" role="img" aria-label="Video still of a hand holding a smartphone">
    <span class="play-btn"></span>
  </div>
  <div class="video-bar"><i></i></div>
  <div class="video-controls"></div>
</div>

<div class="abs divider"></div>

<h2 class="abs section-title col-title about-title">About Us</h2>
<div class="abs about-image" role="img" aria-label="Smartphone surrounded by colourful app icons"></div>
<p class="abs about-copy">At LumoVista, we have been working on a architecture that is scalable, parallelized and runs hierarchy of algo-rithms performing real-time and robust computation in the area of computer vision and machine learning. The scal-ability factor allows us to work across devices like mobile phone/tablet/PC/SmartTV.</p>

<span class="abs news-icon"></span>
<h2 class="abs section-title col-title news-title">Latest News</h2>
<article class="abs news-item" style="top:822px">
  <div class="news-thumb" role="img" aria-label="Hands using a smartphone" style="background:linear-gradient(135deg,#8a8f7e,#3e4a3c)"></div>
  <p class="news-text">Suspendisse pulvinar nisi dui, ultricies sed ultrices nec.</p>
  <p class="news-date" style="top:44px">December 17, 2012</p>
</article>
<article class="abs news-item" style="top:903px">
  <div class="news-thumb" role="img" aria-label="Man talking on a mobile phone" style="background:linear-gradient(135deg,#d8b9a0,#6d4f3d)"></div>
  <p class="news-text">Suspendisse pulvinar nisi dui, ultricies sed ultrices nec.</p>
  <p class="news-date" style="top:44px">December 17, 2012</p>
</article>
<article class="abs news-item" style="top:984px">
  <div class="news-thumb" role="img" aria-label="Man outdoors holding a phone" style="background:linear-gradient(#9fc3e6,#7a9a5a)"></div>
  <p class="news-text">Suspendisse pulvinar nisi dui, ultricies sed ultrices nec.</p>
  <p class="news-date" style="top:44px">December 17, 2012</p>
</article>
<div class="abs view-all" style="left:422px;width:306px"><a>View All</a></div>

<span class="abs tweet-icon"></span>
<h2 class="abs section-title col-title tweets-title">Latest Tweets</h2>
<article class="abs tweet" style="top:823px">
  <div class="tweet-avatar" role="img" aria-label="User avatar" style="background:#4bb3d6"></div>
  <p class="tweet-text"><span class="user">Itaque earum rerum hic</span> tenetur a sapiente delectus, ut aut reiciendis voluptatibus maiores riores modi tempora <a>http://www.loremvale.com/ ut/labore/4et</a> dolore magnam.</p>
  <p class="tweet-meta">2 minutes ago · reply · retweet · favorite</p>
</article>
<article class="abs tweet" style="top:944px">
  <div class="tweet-avatar" role="img" aria-label="User avatar" style="background:linear-gradient(#ddd,#8a2b2b)"></div>
  <p class="tweet-text"><span class="user">Itaque earum rerum hic</span> tenetur a sapiente delectus, ut aut reiciendis voluptatibus maiores riores modi tempora <a>http://www.loremvale.com/ ut/labore/4et</a> dolore magnam.</p>
  <p class="tweet-meta">2 minutes ago · reply · retweet · favorite</p>
</article>
<div class="abs view-all" style="left:752px;width:306px"><a>View All</a></div>

<footer class="abs site-footer"></footer>
<p class="abs footer-nav">Home &nbsp;|&nbsp; About us &nbsp;|&nbsp; Services &nbsp;|&nbsp; Product &nbsp;|&nbsp; Contact</p>
<p class="abs copyright">Copyright &nbsp;©&nbsp; 2012 &nbsp;www.prism48.com &nbsp;All rights reserved.</p>
<span class="abs social" style="left:964px"></span>
<span class="abs social" style="left:1000px"></span>
<span class="abs social" style="left:1036px"></span>

</body>
</html>
```